business card deign

Logo needs the following on it.
1. attached logo
2. Tagline - "From the cooler to the campfire...we've got you covered!"
3. Name- Dalton Pikes, Founder and CPO
4. Address - 412 E. Carver Avenue, Ste 2207, Tampa, FL. 33917
5. Phone - 555.318.4726

```html
<!DOCTYPE html>
<html lang="en">
<head>
<meta charset="UTF-8">
<title>Boundry Business Card</title>
<link href="https://fonts.googleapis.com/css2?family=Montserrat:wght@300;400;700&family=Oswald:wght@600&display=swap" rel="stylesheet">
<style>
  :root {
    --ink: #111111;
    --paper: #ffffff;
    --stage: #e9e7e3;
    --back-dark: #1c1c1c;
    --back-mid: #2a2a2a;
    --back-light: #4a4a4a;
    --mascot-dark: #151515;
    --mascot-mid: #2e2e2e;
  }
  * { box-sizing: border-box; margin: 0; padding: 0; }
  html, body { width: 1200px; height: 931px; overflow: hidden; }
  body {
    background: var(--stage);
    font-family: "Montserrat", sans-serif;
    color: var(--ink);
    position: relative;
  }
  .card {
    position: absolute;
    left: 250px;
    width: 700px;
    height: 400px;
    border-radius: 26px;
    overflow: hidden;
    box-shadow: 0 6px 18px rgba(0,0,0,0.18);
  }
  /* Back */
  .card-back { top: 40px; background: var(--back-dark); }
  .back-pattern {
    position: absolute; inset: 0;
    background: linear-gradient(115deg, var(--back-dark) 0%, var(--back-mid) 55%, var(--back-light) 100%);
  }
  .back-brand {
    position: absolute;
    left: 0; right: 0; top: 176px;
    text-align: center;
    font-family: "Oswald", sans-serif;
    font-weight: 600;
    font-size: 38px;
    letter-spacing: 14px;
    color: var(--paper);
  }
  /* Front */
  .card-front { top: 491px; background: var(--paper); }
  .brand {
    position: absolute;
    left: 52px; top: 38px;
    font-family: "Oswald", sans-serif;
    font-weight: 600;
    font-size: 48px;
    letter-spacing: 22px;
    line-height: 1;
  }
  .identity { position: absolute; left: 78px; top: 118px; }
  .person-name { font-weight: 700; font-size: 30px; line-height: 1.1; }
  .person-role { font-weight: 300; font-size: 20px; margin-top: 2px; }
  .contacts { list-style: none; margin-top: 8px; margin-left: 22px; }
  .contacts li {
    display: flex; align-items: center; gap: 10px;
    font-weight: 300; font-size: 19px; line-height: 1.45;
  }
  .contacts svg { width: 17px; height: 17px; flex: none; }
  .address {
    font-style: normal; font-weight: 300; font-size: 19px;
    line-height: 1.3; margin-top: 10px; margin-left: 48px;
  }
  .mascot-area {
    position: absolute;
    left: 470px; top: 20px;
    width: 210px; height: 290px;
    border-radius: 40% 40% 12% 12%;
    background: linear-gradient(180deg, var(--mascot-mid) 0%, var(--mascot-dark) 100%);
  }
  .rule {
    position: absolute; left: 0; right: 0; bottom: 60px;
    height: 3px; background: var(--ink);
  }
  .tagline-band {
    position: absolute; left: 0; right: 0; bottom: 0;
    height: 52px; background: var(--ink);
    display: flex; align-items: center; justify-content: flex-end;
    padding-right: 40px;
    color: var(--paper); font-weight: 400; font-size: 17px;
  }
</style>
</head>
<body>
  <section class="card card-back">
    <div class="back-pattern" role="img" aria-label="Repeating pattern of brand mascot silhouettes fading from black to grey"></div>
    <div class="back-brand">BOUNDRY</div>
  </section>

  <section class="card card-front">
    <div class="brand">BOUNDRY</div>
    <div class="identity">
      <div class="person-name">Dalton Pikes</div>
      <div class="person-role">Founder and CPO</div>
      <ul class="contacts">
        <li>
          <svg viewBox="0 0 24 24"><path fill="currentColor" d="M6.6 10.8a15 15 0 0 0 6.6 6.6l2.2-2.2a1 1 0 0 1 1-.25 11.4 11.4 0 0 0 3.6.57 1 1 0 0 1 1 1V20a1 1 0 0 1-1 1A17 17 0 0 1 3 4a1 1 0 0 1 1-1h3.5a1 1 0 0 1 1 1c0 1.25.2 2.45.57 3.6a1 1 0 0 1-.25 1z"/></svg>
          555.318.4726
        </li>
        <li>
          <svg viewBox="0 0 24 24"><path fill="currentColor" d="M2 5h20v14H2zm2 2v.5l8 5 8-5V7l-8 5z"/></svg>
          info@email.com
        </li>
        <li>
          <svg viewBox="0 0 24 24" fill="none" stroke="currentColor" stroke-width="2"><circle cx="12" cy="12" r="9"/><path d="M3 12h18M12 3c3 3 3 15 0 18M12 3c-3 3-3 15 0 18"/></svg>
          www.websitename.com
        </li>
      </ul>
      <address class="address">412 E. Carver Avenue, Ste 2207,<br>Tampa, FL. 33917</address>
    </div>
    <div class="mascot-area" role="img" aria-label="Large black mascot silhouette illustration"></div>
    <div class="rule"></div>
    <div class="tagline-band">From the cooler to the campfire...we've got you covered!</div>
  </section>
</body>
</html>
```